Mira Bloom Fitness Coaching Project

I am a personal trainer based in London. My services include one-on-one PT sessions, bootcamps.
I would like the design to be minimalistic. With light colours: white, pink, purple.
I specialise in weight loss, flexibility, mobility.

Tessa Brogan
Personal Trainer
Email: tessa.brogan@quellmail.com
tel: 07700218493
Instagram: Mira Bloom

Target Market(s)

adults, mostly females (age 18-50).

Industry/Entity Type

Fitness

Contact Information for Business Card

Tessa Brogan
Personal Trainer
tel: 07700218493
Instagram: Mira Bloom

Font styles to use
Serif

Colors
eea4c8
fbd4d5
fdf9cf
cfeae6
cee9f5

Requirements
Nice to have
• minimalistic style
• easy to read and remember

```html
<!DOCTYPE html>
<html lang="en">
<head>
<meta charset="utf-8">
<title>Mira Bloom Fitness Coaching – Business Card</title>
<link rel="stylesheet" href="https://fonts.googleapis.com/css2?family=Open+Sans:wght@400;700&display=swap">
<style>
  :root {
    --page-bg: #e9e9eb;
    --card-back: #d3e9f4;
    --ink: #1f5a75;
    --ink-soft: #2f6d88;
    --divider: #a9cbd9;
    --band: #d6efeb;
    --photo-pink: #e79ac2;
    --photo-teal: #8fdcd6;
    --photo-mint: #b7ebe4;
  }
  * { box-sizing: border-box; margin: 0; padding: 0; }
  html, body {
    width: 1200px; height: 900px; overflow: hidden;
    background: var(--page-bg);
  }
  .sheet {
    position: relative; width: 1200px; height: 900px;
    display: flex; align-items: center; justify-content: center; gap: 50px;
  }
  .card {
    position: relative; width: 525px; height: 300px;
    border-radius: 22px; overflow: hidden;
    box-shadow: 0 6px 18px rgba(0,0,0,0.12);
  }

  /* Contact side */
  .card--contact { background: var(--card-back); }
  .brand-mark {
    position: absolute; left: 0; top: 0; width: 270px; height: 300px;
    display: flex; align-items: center; justify-content: center; gap: 10px;
  }
  .brand-mark__dot {
    width: 14px; height: 14px; border-radius: 50%; background: var(--ink); flex: none;
  }
  .brand-mark__name {
    font-family: "Open Sans", sans-serif; font-weight: 400; font-size: 24px;
    color: var(--ink);
  }
  .divider {
    position: absolute; left: 272px; top: 60px; width: 1px; height: 180px;
    background: var(--divider);
  }
  .contact {
    position: absolute; left: 300px; top: 88px;
    font-family: "Open Sans", sans-serif; color: var(--ink);
  }
  .contact__name { font-weight: 700; font-size: 19px; letter-spacing: 0.5px; line-height: 1.1; }
  .contact__role { font-size: 13px; color: var(--ink-soft); margin-bottom: 10px; }
  .contact__line {
    display: flex; align-items: center; gap: 8px;
    font-size: 13.5px; line-height: 1.55;
  }
  .contact__line svg { width: 12px; height: 12px; flex: none; fill: var(--ink); }
  .contact__social-dot {
    width: 14px; height: 14px; border-radius: 50%; background: var(--ink); flex: none;
  }
  .contact__line--social { margin-top: 6px; }

  /* Brand side */
  .card--brand { background: var(--band); }
  .brand-photo {
    position: absolute; left: 0; top: 0; width: 100%; height: 230px;
    background: linear-gradient(168deg, var(--photo-pink) 0%, var(--photo-pink) 38%, var(--photo-teal) 52%, var(--photo-mint) 100%);
  }
  .brand-name {
    position: absolute; left: 0; right: 0; top: 100px;
    display: flex; align-items: center; justify-content: center; gap: 10px;
    font-family: "Open Sans", sans-serif; font-weight: 400; font-size: 26px;
    color: var(--ink);
  }
  .brand-name__dot {
    width: 14px; height: 14px; border-radius: 50%; background: var(--ink); flex: none;
  }
  .specialties {
    position: absolute; left: 0; right: 0; bottom: 26px;
    display: flex; justify-content: center; gap: 18px;
    font-family: "Open Sans", sans-serif; font-size: 14px; color: var(--ink);
  }
  .specialties li { list-style: none; display: flex; align-items: center; gap: 7px; }
  .specialties li::before {
    content: ""; width: 7px; height: 7px; border-radius: 50%; background: var(--ink);
  }
</style>
</head>
<body>
<main class="sheet">
  <section class="card card--contact">
    <div class="brand-mark">
      <span class="brand-mark__dot"></span>
      <span class="brand-mark__name">Mira Bloom</span>
    </div>
    <div class="divider"></div>
    <div class="contact">
      <p class="contact__name">TESSA BROGAN</p>
      <p class="contact__role">Personal Trainer</p>
      <p class="contact__line">
        <svg viewBox="0 0 24 24" aria-hidden="true"><path d="M6.6 10.8a15.1 15.1 0 0 0 6.6 6.6l2.2-2.2a1 1 0 0 1 1-.25 11.4 11.4 0 0 0 3.6.57 1 1 0 0 1 1 1V20a1 1 0 0 1-1 1A17 17 0 0 1 3 4a1 1 0 0 1 1-1h3.5a1 1 0 0 1 1 1c0 1.25.2 2.45.57 3.57a1 1 0 0 1-.25 1z"/></svg>
        07700218493
      </p>
      <p class="contact__line">
        <svg viewBox="0 0 24 24" aria-hidden="true"><path d="M2 5h20v14H2z"/><path d="M3 6l9 7 9-7" fill="none" stroke="var(--card-back)" stroke-width="1.6"/></svg>
        tessa.brogan@quellmail.com
      </p>
      <p class="contact__line contact__line--social">
        <span class="contact__social-dot"></span>
        Mira Bloom
      </p>
    </div>
  </section>

  <section class="card card--brand">
    <div class="brand-photo" role="img" aria-label="Photo of a woman exercising in front of a pink and teal painted wall"></div>
    <p class="brand-name">
      <span class="brand-name__dot"></span>
      Mira Bloom Fitness Coaching
    </p>
    <ul class="specialties">
      <li>Weight Loss</li>
      <li>Flexibility</li>
      <li>Mobility</li>
    </ul>
  </section>
</main>
</body>
</html>
```